Stationary design for boutique production house

We need a stationary design for our production house, 'Lorno Productions' based in Singapore. We produce microfilms as well as podcasts, talkshows and events. Our logo is a stylized icon of our director, who is also the executive producer and host of our programs, Lorno. Our main company colors are Red, Black and white. We would like a clean, minimalist design incorporating our existing company logo that conveys a sense of urbanism and elegance.

Logo and font files are attached. f

Target Market(s)

We focus on lifestyle media rather than entertainment.

Industry/Entity Type

Boutique

Font styles to use
Serif
Sans Serif

Colors
ec1f27
ffffff
000000

Requirements
Must have
• Our company logo and at least one of our company colors.
Nice to have
• Our address and contact information.
Should not have
• Changes made to the company logo (using only certain parts of it is fine though)

```html
<!DOCTYPE html>
<html lang="en">
<head>
<meta charset="utf-8">
<title>Lorno Productions – Business Card</title>
<link href="https://fonts.googleapis.com/css2?family=Jost:wght@400;500&display=swap" rel="stylesheet">
<style>
  :root {
    --red: #d0161d;
    --black: #1c1a1b;
    --white: #ffffff;
    --paper: #f6f6f6;
    --backdrop: #4a4a4a;
    --muted: #555555;
  }
  html, body {
    margin: 0;
    padding: 0;
    width: 1200px;
    height: 750px;
    overflow: hidden;
    background: var(--backdrop);
    font-family: "Jost", "Futura", sans-serif;
  }
  .canvas {
    position: relative;
    width: 1200px;
    height: 750px;
  }
  .card {
    position: absolute;
    top: 228px;
    width: 461px;
    height: 262px;
    background: var(--paper);
    overflow: hidden;
  }
  .card--front { left: 124px; }
  .card--back { left: 595px; }

  .front-bands {
    position: absolute;
    inset: 0;
  }
  .contact {
    position: absolute;
    left: 28px;
    top: 0;
    color: var(--white);
  }
  .contact__name {
    position: absolute;
    top: 32px;
    margin: 0;
    font-size: 18px;
    font-weight: 400;
    letter-spacing: 0.2px;
    white-space: nowrap;
  }
  .contact__role {
    position: absolute;
    top: 58px;
    margin: 0;
    font-size: 13px;
    white-space: nowrap;
  }
  .contact__address {
    position: absolute;
    top: 98px;
    margin: 0;
    font-size: 12px;
    line-height: 16px;
    font-style: normal;
    white-space: nowrap;
  }
  .contact__list {
    position: absolute;
    top: 142px;
    margin: 0;
    padding: 0;
    list-style: none;
    font-size: 12px;
    white-space: nowrap;
  }
  .contact__item {
    display: flex;
    align-items: center;
    height: 18.6px;
  }
  .contact__icon {
    width: 12px;
    height: 12px;
    margin-right: 9px;
    fill: var(--white);
  }

  .wordmark {
    position: absolute;
    display: flex;
    align-items: center;
    gap: 7px;
    color: var(--black);
    font-weight: 500;
    white-space: nowrap;
  }
  .wordmark__dot {
    width: 9px;
    height: 9px;
    border-radius: 50%;
    background: var(--red);
  }
  .card--front .wordmark {
    left: 258px;
    top: 118px;
    font-size: 20px;
  }
  .card--back .wordmark {
    left: 50%;
    top: 112px;
    transform: translateX(-50%);
    font-size: 26px;
  }
  .web {
    position: absolute;
    left: 0;
    right: 0;
    top: 223px;
    text-align: center;
    font-size: 11px;
    letter-spacing: 5px;
    color: var(--muted);
  }
</style>
</head>
<body>
<main class="canvas">
  <section class="card card--front" aria-label="Card front">
    <svg class="front-bands" viewBox="0 0 461 262" aria-hidden="true">
      <path d="M0 0 H240 Q170 131 260 262 H0 Z" fill="var(--black)"/>
      <path d="M0 0 H232 Q170 131 228 262 H0 Z" fill="var(--red)" stroke="var(--white)" stroke-width="2"/>
    </svg>
    <div class="contact">
      <h1 class="contact__name">MARA QUILL</h1>
      <p class="contact__role">CEO/FOUNDER</p>
      <address class="contact__address">42 Keong Saik Road<br>Singapore 089142</address>
      <ul class="contact__list">
        <li class="contact__item">
          <svg class="contact__icon" viewBox="0 0 24 24"><path d="M6.6 10.8c1.4 2.8 3.8 5.2 6.6 6.6l2.2-2.2c.3-.3.7-.4 1-.2 1.1.4 2.3.6 3.6.6.6 0 1 .4 1 1V20c0 .6-.4 1-1 1C10.6 21 3 13.4 3 4c0-.6.4-1 1-1h3.5c.6 0 1 .4 1 1 0 1.3.2 2.5.6 3.6.1.3 0 .7-.2 1z"/></svg>
          6221 4870
        </li>
        <li class="contact__item">
          <svg class="contact__icon" viewBox="0 0 24 24"><path d="M7 1h10a2 2 0 0 1 2 2v18a2 2 0 0 1-2 2H7a2 2 0 0 1-2-2V3a2 2 0 0 1 2-2zm0 3v14h10V4z"/></svg>
          9183 5562
        </li>
        <li class="contact__item">
          <svg class="contact__icon" viewBox="0 0 24 24"><path d="M6 2h12v5H6zM3 9h18a1 1 0 0 1 1 1v8h-4v4H6v-4H2v-8a1 1 0 0 1 1-1zm5 7v4h8v-4z"/></svg>
          6221 4871
        </li>
        <li class="contact__item">
          <svg class="contact__icon" viewBox="0 0 24 24"><path d="M2 5h20v14H2zm2 2v.5l8 5 8-5V7z"/></svg>
          hello@lornostudio.com
        </li>
        <li class="contact__item">
          <svg class="contact__icon" viewBox="0 0 24 24"><path d="M12 2a10 10 0 1 0 0 20 10 10 0 0 0 0-20zm-1 17.9A8 8 0 0 1 4.1 10L9 15v1a2 2 0 0 0 2 2zm6.9-2.5A2 2 0 0 0 16 16h-1v-3a1 1 0 0 0-1-1H8v-2h2a1 1 0 0 0 1-1V7h2a2 2 0 0 0 2-2v-.4a8 8 0 0 1 2.9 12.8z"/></svg>
          www.lornostudio.com
        </li>
      </ul>
    </div>
    <div class="wordmark"><span class="wordmark__dot"></span>Lorno Productions</div>
  </section>

  <section class="card card--back" aria-label="Card back">
    <div class="wordmark"><span class="wordmark__dot"></span>Lorno</div>
    <p class="web">www.lornostudio.com</p>
  </section>
</main>
</body>
</html>
```